Venture 482 - Lumora Book Cover

I am looking for a Lumora book cover for my book about "Venture 482".
The Book is Titled:
Venture 482 Ascended
Shaping Outcomes: Paths To Unlocking Cosmic Truths
Author is Dorian Pell
Here is a book description that may help you understand more about it:
Inspired by the genius of Edwin Marlowe, this comprehensive guide delves into the ancient wisdom and cutting-edge science behind the 482 method, a powerful tool for manifesting your desires. Whether you're seeking personal growth, financial success, or spiritual enlightenment, this book provides advanced techniques and methods to transform your dreams into reality.
Any questions please ask.
Thanks
Owen

```html
<!DOCTYPE html>
<html lang="en">
<head>
<meta charset="utf-8">
<title>Venture 482 Ascended — Dorian Pell</title>
<link rel="stylesheet" href="https://fonts.googleapis.com/css2?family=Cinzel:wght@400;500&family=Quicksand:wght@600&family=Tinos:wght@400;700&display=swap">
<style>
  :root {
    --sky-top: #12434a;
    --sky-mid: #0b2b31;
    --sky-deep: #040a0c;
    --cream: #f6eadf;
    --blush: #f1dcd2;
    --band: #fcf7d9;
    --band-ink: #3b3563;
    --white: #ffffff;
  }
  * { margin: 0; padding: 0; box-sizing: border-box; }
  html, body { width: 805px; height: 1200px; overflow: hidden; background: var(--sky-deep); }
  .cover {
    position: relative;
    width: 805px;
    height: 1200px;
    overflow: hidden;
  }
  .night-sky {
    position: absolute;
    inset: 0;
    background:
      radial-gradient(ellipse 70% 45% at 55% 12%, rgba(40, 110, 120, 0.55), transparent 70%),
      linear-gradient(180deg, var(--sky-top) 0%, var(--sky-mid) 40%, #071719 70%, var(--sky-deep) 100%);
  }
  .series-title {
    position: absolute;
    top: 160px;
    left: 0;
    width: 100%;
    text-align: center;
    font-family: "Cinzel", serif;
    font-weight: 400;
    font-size: 112px;
    line-height: 1;
    color: var(--cream);
    letter-spacing: -0.01em;
  }
  .emblem {
    position: absolute;
    left: 203px;
    top: 256px;
    width: 420px;
    height: 520px;
    border-radius: 50%;
    background: radial-gradient(circle at 50% 50%,
      rgba(10, 30, 34, 0.9) 0%,
      rgba(10, 30, 34, 0.9) 36%,
      rgba(230, 240, 240, 0.35) 40%,
      rgba(200, 220, 222, 0.18) 60%,
      rgba(230, 240, 240, 0.32) 72%,
      rgba(20, 50, 55, 0) 76%);
  }
  .series-number {
    position: absolute;
    top: 484px;
    left: 0;
    width: 826px;
    text-align: center;
    font-family: "Quicksand", sans-serif;
    font-weight: 600;
    font-size: 90px;
    line-height: 1;
    color: var(--white);
  }
  .edition-band {
    position: absolute;
    left: 199px;
    top: 819px;
    width: 427px;
    height: 52px;
    background: var(--band);
    display: flex;
    align-items: center;
    justify-content: center;
    font-family: "Cinzel", serif;
    font-size: 36px;
    color: var(--band-ink);
    letter-spacing: 0.62em;
    padding-left: 0.62em;
  }
  .subtitle {
    position: absolute;
    top: 898px;
    left: 0;
    width: 808px;
    text-align: center;
    font-family: "Tinos", serif;
    color: var(--white);
  }
  .subtitle-lead {
    font-weight: 700;
    font-size: 27px;
    line-height: 34px;
  }
  .subtitle-rest {
    font-weight: 400;
    font-size: 26px;
    line-height: 36px;
  }
  .author {
    position: absolute;
    left: 0;
    top: 1105px;
    width: 805px;
    height: 70px;
  }
  .author text {
    font-family: "Cinzel", serif;
    font-size: 60px;
    fill: var(--blush);
  }
</style>
</head>
<body>
  <main class="cover">
    <div class="night-sky" role="img" aria-label="Deep teal night sky filled with scattered stars"></div>

    <h1 class="series-title">VENTURE</h1>

    <div class="emblem" role="img" aria-label="White line-drawn sacred geometry emblem of interlocking circles, arcs and sun symbols"></div>
    <div class="series-number">482</div>

    <div class="edition-band">ASCENDED</div>

    <h2 class="subtitle">
      <span class="subtitle-lead">SHAPING OUTCOMES:</span><br>
      <span class="subtitle-rest">Paths to unlocking<br>cosmic truths</span>
    </h2>

    <svg class="author" viewBox="0 0 805 70" aria-label="Dorian Pell">
      <text x="55" y="62" textLength="714" lengthAdjust="spacing">DORIAN PELL</text>
    </svg>
  </main>
</body>
</html>
```